Launching a new real estate agency in Monaco

Hello, I am opening a new real estate agency in Monaco. For the purpose of my activity, in order to be known quickly among a fierce competition I need an advertising campaign that will be broadcast in local magazines, newspapers, paper board, etc.

You will find example of pictures of Monaco on which I have the rights and my logo. You can always pick other images that I can buy if the price is reasonable for a commercial use (<200 $)

Please respect the color code.

I wish you good luck and look forward to give you my feedbacks

Reason: Only few projects posted were respecting the brief and of quality. Hoping to receive more in coming days

Target Market(s)

International high-end clientele of all ages, all genders.

Industry/Entity Type

Real Estate Agent

Font styles to use
Serif

Requirements
Must have
• 1/ My logo
• 2/ This message "Un nouveau regard sur l'immobilier" means in English a fresh look at real estate or new eyes on real-estate.
• 3/ My address: 14 rue des Ormeaux, Galerie Bellerive Nord, 98 000 Monaco
• 4/ Phone number: +377.93.48.25.07
• 5/ Website: www.corvano-immo.com.
• 6/ Format: Files should be easily adjustable but I'd like a vertical display to fit easily in Magazines, Poster and billboard. So please work in high resolution !
Nice to have
• Please think about your design in accordance with the message I want to display.
Should not have
• A simple poster with a picture of Monaco that does not take into consideration the message of the advertisement, "Un nouveau regard sur l'immobilier" which means in english, new eyes on real-estate or a new look at real-estate, or new vision at real-estate.

```html
<!DOCTYPE html>
<html lang="fr">
<head>
<meta charset="utf-8">
<title>Corvano Immo – Un nouveau regard sur l'immobilier</title>
<link href="https://fonts.googleapis.com/css2?family=Jost:wght@400;500&display=swap" rel="stylesheet">
<style>
  :root {
    --page-bg: #000000;
    --brand-red: #c8102e;
    --card-dark: #231f20;
    --copper: #d49a84;
    --white: #ffffff;
    --wood-dark: #3b3b3b;
    --wood-light: #7c7c7c;
    --sky-gold: #f4a24a;
    --sky-rose: #e7a79a;
    --sea-violet: #a07aa8;
    --city-plum: #5a3a4a;
    --city-amber: #b9733a;
  }
  * { margin: 0; padding: 0; box-sizing: border-box; }
  html, body {
    width: 1187px; height: 1200px; overflow: hidden;
    background: var(--page-bg);
    font-family: "Jost", "Futura", sans-serif;
  }
  .canvas { position: relative; width: 1187px; height: 1200px; }

  .poster {
    position: absolute; left: 244px; top: 66px; width: 746px; height: 689px;
  }
  .poster__visual { position: relative; height: 499px; overflow: hidden; }
  .poster__view {
    position: absolute; left: 148px; top: 0; width: 458px; height: 100%;
    background: linear-gradient(180deg,
      #f6e1c4 0%, var(--sky-gold) 10%, #e6603a 15%,
      var(--sky-rose) 19%, var(--sea-violet) 32%, #8a6a98 45%,
      var(--city-plum) 62%, var(--city-amber) 80%, #4a2e2a 100%);
  }
  .poster__door {
    position: absolute; top: 0; height: 100%;
    background: linear-gradient(90deg, var(--wood-dark), var(--wood-light) 50%, var(--wood-dark));
  }
  .poster__door--left { left: 0; width: 148px; }
  .poster__door--right { left: 606px; width: 140px; }

  .poster__band {
    height: 190px; background: var(--brand-red); color: var(--white);
    text-align: center; padding-top: 60px;
  }
  .poster__values { font-size: 24px; font-weight: 400; letter-spacing: 0.5px; line-height: 30px; }
  .poster__headline { font-size: 27.5px; font-weight: 500; letter-spacing: 0.3px; line-height: 36px; margin-top: 4px; }

  .card {
    position: absolute; left: 244px; top: 774px; width: 746px; height: 379px;
    background: var(--card-dark); color: var(--white); text-align: center;
  }
  .card__brand {
    position: absolute; top: 96px; left: 0; right: 0;
    display: flex; justify-content: center; align-items: center; gap: 16px;
  }
  .card__brand-mark { width: 28px; height: 28px; background: var(--copper); }
  .card__brand-name {
    font-size: 38px; font-weight: 500; letter-spacing: 4px; color: var(--copper);
  }
  .card__address {
    position: absolute; top: 212px; left: 0; right: 0;
    font-size: 15px; line-height: 19px; font-weight: 400; font-style: normal;
  }
  .card__contact {
    position: absolute; left: 0; right: 0; bottom: 0; height: 32px;
    background: var(--brand-red);
    display: flex; justify-content: center; align-items: center; gap: 26px;
    font-size: 16px;
  }
  .contact-item { display: flex; align-items: center; gap: 5px; }
  .contact-item svg { width: 12px; height: 12px; }
  .icon-phone { fill: var(--white); }
  .icon-web { fill: none; stroke: var(--white); stroke-width: 1.4; }
</style>
</head>
<body>
<main class="canvas">
  <section class="poster">
    <div class="poster__visual">
      <div class="poster__view" role="img" aria-label="Sunset aerial view of Monaco's harbour, sea and lit city towers"></div>
      <div class="poster__door poster__door--left" role="img" aria-label="Weathered wooden door being pushed open by a hand"></div>
      <div class="poster__door poster__door--right" role="img" aria-label="Weathered wooden door being pushed open by a hand"></div>
    </div>
    <div class="poster__band">
      <p class="poster__values">CONFIANCE | ÉTHIQUE | QUALITÉ</p>
      <h1 class="poster__headline">UN NOUVEAU REGARD SUR L'IMMOBILIER</h1>
    </div>
  </section>

  <section class="card">
    <div class="card__brand">
      <span class="card__brand-mark"></span>
      <span class="card__brand-name">CORVANO IMMO</span>
    </div>
    <address class="card__address">
      14 Rue Des Ormeaux<br>
      Galerie Bellerive Nord<br>
      98 000 Monaco
    </address>
    <div class="card__contact">
      <span class="contact-item">
        <svg class="icon-phone" viewBox="0 0 12 12"><path d="M3 1h1.6l1 2.6-1.3 1a6 6 0 0 0 2.6 2.6l1-1.3L10.5 7v1.6A1.5 1.5 0 0 1 9 10.1 8 8 0 0 1 1.5 2.6 1.5 1.5 0 0 1 3 1z"/></svg>
        +377.93.48.25.07
      </span>
      <span class="contact-item">
        <svg class="icon-web" viewBox="0 0 12 12"><circle cx="6" cy="6" r="5"/><path d="M1 6 H11 M6 1 C3 4 3 8 6 11 M6 1 C9 4 9 8 6 11"/></svg>
        www.corvano-immo.com
      </span>
    </div>
  </section>
</main>
</body>
</html>
```